TALMORK

The business want a professional looking business card. We have a scetch we will add but want the extra upgrade, and would like more suggestions for variations of our business cards.

```html
<!DOCTYPE html>
<html lang="en">
<head>
<meta charset="utf-8">
<title>TALMORK – Business Card</title>
<link href="https://fonts.googleapis.com/css2?family=Playfair+Display:wght@700&family=Lato:wght@400&display=swap" rel="stylesheet">
<style>
  :root {
    --backdrop: #8e8e8e;
    --card: #1d1d1d;
    --gold: #c9a042;
    --gold-soft: #d8b24f;
    --text-light: #e6e6e6;
  }
  * { margin: 0; padding: 0; box-sizing: border-box; }
  html, body { width: 1200px; height: 1200px; overflow: hidden; }
  body {
    background: var(--backdrop);
    position: relative;
    font-family: "Lato", sans-serif;
  }
  .card {
    position: absolute;
    left: 281px;
    width: 642px;
    height: 366px;
    background: var(--card);
    border-radius: 20px;
    overflow: hidden;
  }
  .card--front { top: 195px; }
  .card--back { top: 639px; }

  .holder-name {
    position: absolute;
    left: 42px; top: 42px;
    font-family: "Playfair Display", serif;
    font-weight: 700;
    font-size: 27px;
    color: var(--gold);
    white-space: nowrap;
  }
  .holder-role {
    position: absolute;
    left: 42px; top: 79px;
    font-size: 15px;
    color: var(--text-light);
  }
  .divider {
    position: absolute;
    left: 43px; top: 116px;
    width: 73px; height: 1.5px;
    background: var(--gold);
  }
  .contact-list {
    position: absolute;
    left: 42px; top: 136px;
    list-style: none;
  }
  .contact-list li {
    display: flex;
    align-items: center;
    height: 22.5px;
    font-size: 14px;
    color: var(--text-light);
  }
  .contact-list svg { width: 13px; height: 13px; margin-right: 11px; fill: var(--gold); }

  .wordmark {
    font-family: "Playfair Display", serif;
    font-weight: 700;
    color: var(--gold);
    letter-spacing: 0.22em;
    white-space: nowrap;
  }
  .card--front .wordmark {
    position: absolute;
    left: 42px; top: 222px;
    font-size: 38px;
  }
  .since {
    position: absolute;
    font-size: 10px;
    letter-spacing: 0.55em;
    color: var(--text-light);
    white-space: nowrap;
  }
  .card--front .since { left: 127px; top: 303px; }

  .brand-dot {
    position: absolute;
    border-radius: 50%;
    background: var(--gold-soft);
  }
  .card--front .brand-dot { left: 365px; top: 83px; width: 200px; height: 200px; }

  .card--back .brand-dot { left: 281px; top: 91px; width: 80px; height: 80px; }
  .card--back .wordmark {
    position: absolute;
    left: 0; right: 0; top: 198px;
    text-align: center;
    font-size: 48px;
    padding-left: 0.22em;
  }
  .card--back .since { left: 0; right: 0; top: 300px; text-align: center; padding-left: 0.55em; }
</style>
</head>
<body>
  <section class="card card--front">
    <h1 class="holder-name">Arne Lund Haugstad</h1>
    <p class="holder-role">CEO &amp; Founder</p>
    <div class="divider"></div>
    <ul class="contact-list">
      <li><svg viewBox="0 0 24 24"><path d="M6.6 10.8a15 15 0 0 0 6.6 6.6l2.2-2.2a1 1 0 0 1 1-.25 11.4 11.4 0 0 0 3.6.57 1 1 0 0 1 1 1V20a1 1 0 0 1-1 1A17 17 0 0 1 3 4a1 1 0 0 1 1-1h3.5a1 1 0 0 1 1 1c0 1.25.2 2.45.57 3.6a1 1 0 0 1-.25 1z"/></svg>004791234567</li>
      <li><svg viewBox="0 0 24 24"><path d="M2 5h20v14H2z M2 5l10 8 10-8" fill="var(--gold)"/><path d="M3 6l9 7 9-7" fill="none" stroke="#1d1d1d" stroke-width="1.6"/></svg>talmork.llc@mailbox.com</li>
      <li><svg viewBox="0 0 24 24"><circle cx="12" cy="12" r="10"/><path d="M7 7c2 1 3 3 2 5s1 3 2 5M15 4c-1 2 1 3 3 3s2 3 0 5" fill="none" stroke="#1d1d1d" stroke-width="1.8"/></svg>www.talmork.llc</li>
    </ul>
    <div class="wordmark">TALMORK</div>
    <p class="since">SINCE 2026</p>
    <div class="brand-dot" aria-hidden="true"></div>
  </section>

  <section class="card card--back">
    <div class="brand-dot" aria-hidden="true"></div>
    <div class="wordmark">TALMORK</div>
    <p class="since">SINCE 2026</p>
  </section>
</body>
</html>
```